Advanced Therapeutic Massage Therapist

I need a business card advertising my massage services as an advanced therapeutic massage therapist. I offer advanced therapeutic massage, swedish and deep tissue. I want to create a simple, professional and feminine card. I like bright colours and creativity.

I prefer a bold and experimental approach rather than something status-quo. A card to suggest therapeutic healing through dynamic massage. Motifs, shapes or layout which suggest movement and flow.
Updates

Target Market(s)

Everybody!

Industry/Entity Type

Health And Wellness

Contact Information for Business Card

The card should include:
My name, logo, services offered and my contact details.

Sláine Dunleavy
Massage Therapist

- Swedish - Deep Tissue - Advanced Therapeutic

Phone: (+353) 87 216 4093
Email: regenerate@slainedunleavy-example.com
Website: www.slainedunlevy-example.com

Font styles to use
Serif
Sans Serif
Decorative
Script

Colors

Designer to choose colors to be used in the design.

Requirements
Must have
• An example may contain something like this, yet concise:
• "Sláine Dunleavy
• Massage Therapist
• - Swedish - Deep Tissue - Advanced Therapeutic"
Nice to have
• This sentence is optional:
• Imagery such as a logo or symbol. I have attached a file containing a logo I had produced however the name is incorrect now as it is "Sláine" not "Nelly". It could be edited to change it to Sláine.
• I have sent the file as .psd .jpg. .pdf and .png
• I like when the card conveys energy, movement, pressure points, flow etc.
• I just like the designer to follow their own style and ideas. I like bright colours but must have a lot of a base colour to offset it. I really prefer them to follow their own inspiration. That is my preference.
Should not have
• Pine trees, non-native trees to Britain and Ireland, exotic flowers or animals that are not native to Britain and Ireland.
• I don't like brown as the background colour of the card.
• The cars shouldn't look like a wedding invitation i.e too many floral type designs.

```html
<!DOCTYPE html>
<html lang="en">
<head>
<meta charset="utf-8">
<title>Sláine Dunleavy – Business Card</title>
<link rel="stylesheet" href="https://fonts.googleapis.com/css2?family=Great+Vibes&family=Questrial&display=swap">
<style>
  :root {
    --stage: #666666;
    --mint-light: #bfe9dc;
    --mint: #9fdcc9;
    --mint-deep: #7fcfb8;
    --charcoal: #222222;
    --gold: #f2c94c;
    --gold-deep: #c9932e;
    --ink: #2b2b2b;
    --white: #ffffff;
    --service: #5fc4a0;
  }
  * { margin: 0; padding: 0; box-sizing: border-box; }
  html, body { width: 1200px; height: 550px; overflow: hidden; background: var(--stage); }
  .stage { position: relative; width: 1200px; height: 550px; background: var(--stage); }

  .card { position: absolute; top: 157px; width: 392px; height: 235px; overflow: hidden; }
  .card--front { left: 194px; }
  .card--back { left: 614px; background: var(--charcoal); }

  .watercolour {
    position: absolute; inset: 0;
    background:
      radial-gradient(ellipse at 25% 30%, var(--mint-light) 0%, transparent 55%),
      radial-gradient(ellipse at 75% 70%, var(--mint-deep) 0%, transparent 60%),
      linear-gradient(135deg, var(--mint) 0%, var(--mint-light) 50%, var(--mint) 100%);
  }

  .mark {
    position: absolute; border-radius: 50%;
    display: flex; align-items: center; justify-content: center;
    background: radial-gradient(circle, var(--mint-light) 0%, var(--mint) 100%);
    border: 2px solid var(--gold-deep);
  }
  .mark__name {
    font-family: "Great Vibes", cursive; color: var(--gold-deep);
    font-size: 17px; text-align: center; line-height: 1;
  }
  .card--front .mark { left: 140px; top: 59px; width: 112px; height: 112px; }
  .card--back .mark { left: 25px; top: 59px; width: 128px; height: 128px; }

  .name {
    position: absolute; font-family: "Great Vibes", cursive;
    font-size: 22px; line-height: 1; white-space: nowrap; transform: translateX(-50%);
  }
  .role {
    position: absolute; font-family: "Questrial", sans-serif;
    font-size: 9px; letter-spacing: 0.8px; white-space: nowrap; transform: translateX(-50%);
  }
  .card--front .name { left: 196px; top: 161px; color: var(--ink); }
  .card--front .role { left: 196px; top: 182px; color: var(--ink); }
  .card--back .name { left: 290px; top: 139px; color: var(--white); }
  .card--back .role { left: 290px; top: 167px; color: var(--white); }

  .wave { position: absolute; inset: 0; }

  .contact {
    position: absolute; right: 18px; top: 14px; list-style: none; text-align: right;
    font-family: "Questrial", sans-serif; font-size: 10.5px; line-height: 17px; color: var(--ink);
  }

  .services {
    position: absolute; left: 0; right: 0; top: 212px;
    display: flex; align-items: center; justify-content: center; gap: 10px;
    font-family: "Questrial", sans-serif; font-size: 10px; color: var(--service);
  }
  .services__rule { width: 36px; height: 1.5px; background: var(--white); }
</style>
</head>
<body>
<main class="stage">

  <section class="card card--front" aria-label="Card front">
    <div class="watercolour" role="img" aria-label="Soft mint watercolour wash background"></div>
    <div class="mark"><span class="mark__name">Sláine<br>Dunleavy</span></div>
    <h1 class="name">Sláine Dunleavy</h1>
    <p class="role">massage therapist</p>
  </section>

  <section class="card card--back" aria-label="Card back">
    <svg class="wave" viewBox="0 0 392 235" width="392" height="235" aria-hidden="true">
      <defs>
        <linearGradient id="mintWash" x1="0" y1="0" x2="1" y2="1">
          <stop offset="0" stop-color="#bfe9dc"/>
          <stop offset="1" stop-color="#9fdcc9"/>
        </linearGradient>
        <linearGradient id="goldSheen" x1="0" y1="0" x2="1" y2="0">
          <stop offset="0" stop-color="#c9932e"/>
          <stop offset="0.5" stop-color="#f2c94c"/>
          <stop offset="1" stop-color="#f7d65a"/>
        </linearGradient>
      </defs>
      <path d="M0 0 H392 V104 C300 90 230 30 120 18 C70 13 30 20 0 32 Z" fill="url(#mintWash)"/>
      <path d="M0 0 H260 C180 4 90 8 0 30 Z" fill="#222222"/>
      <path d="M0 34 C80 14 170 16 240 50 C290 74 340 94 392 100 L392 108 C330 102 280 82 236 60 C170 28 90 26 0 50 Z" fill="url(#goldSheen)"/>
      <path d="M20 58 C100 32 180 42 250 76 C300 98 350 110 392 112 L392 116 C340 116 290 104 240 82 C180 54 100 44 20 58 Z" fill="url(#goldSheen)"/>
    </svg>

    <ul class="contact">
      <li>slaine@slainedunleavy-example.com</li>
      <li>slainedunleavy-example.com</li>
      <li>(+353) 87 216 4093</li>
    </ul>

    <div class="mark"><span class="mark__name">Sláine<br>Dunleavy</span></div>
    <h2 class="name">Sláine Dunleavy</h2>
    <p class="role">massage therapist</p>

    <p class="services">
      <span class="services__rule"></span>
      <span>Swedish - Deep Tissue - Advanced Therapeutic</span>
      <span class="services__rule"></span>
    </p>
  </section>

</main>
</body>
</html>
```